Vantrel Intergrated Marketing Stationary Design Contest

We require a very professional looking stationary set to include: letterhead, compliments slip and business cards (double sided bus cards).

Files should be supplied on either Illustrator or InDesign.

We are interested in perhaps encorporating a faint watermark with the letter q or the logo, but it isnt a pre-requisite

Target Market(s)

Business owners seeking professional marketing services

Industry/Entity Type

Marketing

Requirements
Must have
• Concurrent theme wiht business cards, letterhead and comp slip. Must be an editable document for future ammendment
Should not have
• No use of times new roman or similar fonts

```html
<!DOCTYPE html>
<html lang="en">
<head>
<meta charset="utf-8">
<title>Vantrel Intergrated Marketing – Stationery Set</title>
<link rel="stylesheet" href="https://fonts.googleapis.com/css2?family=Open+Sans:ital,wght@0,400;0,600;0,700;1,600&display=swap">
<style>
  :root {
    --brand-orange: #f15a29;
    --ink: #1a1a1a;
    --logo-grey: #3d3d3d;
    --paper: #ffffff;
    --edge: #2b2b2b;
  }
  * { box-sizing: border-box; margin: 0; padding: 0; }
  html, body { width: 1200px; height: 1200px; overflow: hidden; background: var(--paper); }
  body { position: relative; font-family: "Open Sans", Arial, sans-serif; color: var(--ink); }

  .sheet { position: absolute; background: var(--paper); border: 1.2px solid var(--edge); }
  .letterhead { left: 157px; top: 24px; width: 661px; height: 936px; }
  .comp-slip { left: 359px; top: 347px; width: 661px; height: 311px; }
  .card-front { left: 278px; top: 990px; width: 279px; height: 172px; }
  .card-back { left: 611px; top: 990px; width: 284px; height: 174px; }

  .brand { position: absolute; display: flex; align-items: center; gap: 8px; }
  .brand-dot { border-radius: 50%; background: var(--brand-orange); flex: none; }
  .brand-name { font-weight: 400; color: var(--logo-grey); letter-spacing: 0.14em; line-height: 1; }

  .letterhead .brand { left: 35px; top: 36px; }
  .letterhead .brand-dot { width: 40px; height: 40px; }
  .letterhead .brand-name { font-size: 30px; }

  .comp-slip .brand { left: 33px; top: 37px; }
  .comp-slip .brand-dot { width: 36px; height: 36px; }
  .comp-slip .brand-name { font-size: 27px; }

  .comp-title {
    position: absolute; left: 73px; top: 78px;
    font-size: 14.5px; font-weight: 600; font-style: italic;
    color: var(--brand-orange); letter-spacing: -0.01em;
  }

  .contact { position: absolute; text-align: right; font-size: 8.4px; line-height: 11px; }
  .contact .company { color: var(--brand-orange); font-weight: 700; }
  .contact .gap { margin-top: 8px; }
  .contact .label { color: var(--brand-orange); }
  .letterhead .contact { right: 160px; top: 60px; }
  .comp-slip .contact { right: 30px; top: 36px; }

  .card-front .brand { left: 13px; top: 75px; gap: 5px; }
  .card-front .brand-dot { width: 21px; height: 21px; }
  .card-front .brand-name { font-size: 15px; }

  .card-details { position: absolute; left: 135px; top: 44px; font-size: 7px; line-height: 8.6px; }
  .card-details .person { color: var(--brand-orange); font-weight: 700; font-size: 11.5px; line-height: 12px; }
  .card-details .role { font-size: 8px; line-height: 10px; }
  .card-details .company { color: var(--brand-orange); font-weight: 700; margin-top: 12px; }
  .card-details .gap { margin-top: 6px; }
  .card-details .label { color: var(--brand-orange); font-weight: 600; display: inline-block; width: 12px; }

  .card-mark {
    position: absolute; left: 174px; top: 62px; width: 92px; height: 92px;
    background: var(--brand-orange);
  }
</style>
</head>
<body>

  <section class="sheet letterhead" aria-label="Letterhead">
    <div class="brand">
      <span class="brand-dot"></span>
      <span class="brand-name">vantrel</span>
    </div>
    <address class="contact" style="font-style:normal">
      <div class="company">Vantrel Intergrated Marketing</div>
      <div>Central Offices</div>
      <div>Harbour Lane, Oakridge, West Riding, OK4 7RT</div>
      <div class="gap"><span class="label">W:</span> www.vantrelim.co.uk &nbsp; <span class="label">E:</span> &nbsp;hello@vantrelim.co.uk</div>
      <div><span class="label">T:</span> &nbsp;01632 960417 &nbsp;&nbsp; <span class="label">F:</span> &nbsp;01632 960418</div>
      <div class="gap">Company registration: 4815026 &nbsp;&nbsp;&nbsp; Vat No: 771 2048 55</div>
      <div>Trading as a division of Brenmoor Ltd</div>
    </address>
  </section>

  <section class="sheet comp-slip" aria-label="Compliments slip">
    <div class="brand">
      <span class="brand-dot"></span>
      <span class="brand-name">vantrel</span>
    </div>
    <div class="comp-title">WITH COMPLEMENTS</div>
    <address class="contact" style="font-style:normal">
      <div class="company">Vantrel Intergrated Marketing</div>
      <div>Central Offices</div>
      <div>Harbour Lane, Oakridge, West Riding, OK4 7RT</div>
      <div class="gap"><span class="label">W:</span> www.vantrelim.co.uk &nbsp; <span class="label">E:</span> &nbsp;hello@vantrelim.co.uk</div>
      <div><span class="label">T:</span> &nbsp;01632 960417 &nbsp;&nbsp; <span class="label">F:</span> &nbsp;01632 960418</div>
      <div class="gap">Company registration: 4815026 &nbsp;&nbsp;&nbsp; Vat No: 771 2048 55</div>
      <div>Trading as a division of Brenmoor Ltd</div>
    </address>
  </section>

  <section class="sheet card-front" aria-label="Business card front">
    <div class="brand">
      <span class="brand-dot"></span>
      <span class="brand-name">vantrel</span>
    </div>
    <div class="card-details">
      <div class="person">Mara Holloway</div>
      <div class="role">General Manager</div>
      <div class="company">Vantrel Intergrated Marketing</div>
      <div>Central Offices</div>
      <div>Harbour Lane, Oakridge, West Riding</div>
      <div>OK4 7RT</div>
      <div class="gap"><span class="label">W:</span>www.vantrelim.co.uk</div>
      <div><span class="label">E:</span>mara@vantrelim.co.uk</div>
      <div><span class="label">T:</span>01632 960417</div>
      <div><span class="label">F:</span>01632 960418</div>
    </div>
  </section>

  <section class="sheet card-back" aria-label="Business card back">
    <div class="card-mark"></div>
  </section>

</body>
</html>
```